Brickfield real estate investment company needs a poster design

We would like a poster design size 18 x 24.
Poster wording -
I WANT TO BUY YOUR ( finish with logo) logo uploaded
website- www.brickfield.example
phone # 555-218-7043 ( color red for the phone number)
we would like to see the poster on 2 different backgrounds
Yellow background
White background
horizontal

```html
<!DOCTYPE html>
<html lang="en">
<head>
<meta charset="utf-8">
<title>Brickfield – I Want to Buy Your House</title>
<link rel="stylesheet" href="https://fonts.googleapis.com/css2?family=Bevan&family=Open+Sans:wght@700;800&display=swap">
<style>
  :root {
    --paper: #ffffff;
    --ink: #111111;
    --signal-red: #f20f0f;
    --wall-grey: #b4b1ad;
    --wall-shadow: #8f8c88;
    --roof-brown: #9a5730;
    --brick: #b9623a;
  }
  * { margin: 0; padding: 0; box-sizing: border-box; }
  html, body { width: 1200px; height: 900px; overflow: hidden; background: var(--paper); }
  .poster {
    position: relative;
    width: 1200px;
    height: 900px;
    background: var(--paper);
    font-family: "Open Sans", Arial, sans-serif;
    color: var(--ink);
  }
  .headline {
    position: absolute;
    top: 52px;
    left: 0;
    width: 100%;
    text-align: center;
    font-family: "Bevan", Georgia, serif;
    font-size: 58px;
    line-height: 1;
    letter-spacing: 1px;
    color: var(--ink);
  }
  .brand-name {
    position: absolute;
    top: 148px;
    left: 0;
    width: 100%;
    text-align: center;
    font-family: "Open Sans", Arial, sans-serif;
    font-weight: 800;
    font-size: 82px;
    line-height: 1;
    text-transform: uppercase;
    color: var(--ink);
  }
  .house-illustration {
    position: absolute;
    left: 250px;
    top: 250px;
    width: 700px;
    height: 420px;
    background:
      linear-gradient(180deg,
        var(--roof-brown) 0%,
        var(--brick) 24%,
        var(--wall-grey) 46%,
        var(--wall-grey) 78%,
        var(--wall-shadow) 100%);
    -webkit-mask-image: radial-gradient(ellipse 52% 54% at 50% 50%, #000 62%, transparent 100%);
    mask-image: radial-gradient(ellipse 52% 54% at 50% 50%, #000 62%, transparent 100%);
  }
  .call-label {
    position: absolute;
    top: 677px;
    left: 0;
    width: 100%;
    text-align: center;
    font-weight: 700;
    font-size: 45px;
    line-height: 1;
    color: var(--signal-red);
  }
  .phone-number {
    position: absolute;
    top: 718px;
    left: 0;
    width: 100%;
    text-align: center;
    font-weight: 700;
    font-size: 96px;
    line-height: 1;
    color: var(--signal-red);
  }
  .web-band {
    position: absolute;
    left: 0;
    bottom: 0;
    width: 100%;
    height: 60px;
    background: var(--signal-red);
    display: flex;
    align-items: center;
    justify-content: center;
  }
  .web-address {
    font-weight: 700;
    font-size: 29px;
    color: var(--paper);
  }
</style>
</head>
<body>
  <main class="poster">
    <h1 class="headline">I WANT TO BUY YOUR</h1>
    <div class="brand-name">Brickfield</div>
    <div class="house-illustration" role="img" aria-label="Illustration of a run-down house with a broken tiled roof, boarded-up windows, cracked walls and a cracked chimney"></div>
    <p class="call-label">CALL US!</p>
    <p class="phone-number">555-218-7043</p>
    <footer class="web-band">
      <span class="web-address">www.brickfield.example</span>
    </footer>
  </main>
</body>
</html>
```